full stationary design for a modern sleek design company

we are a design company that does modern minimalistic interior design works as well as other design services for high end clients.
we need a full stationary design including and not limited to (double sided business card, letter head, envelopes, documents folder...etc) that reflects the modern style design we do.
sleek modern and minimalistic is the requirements.
Updates

please use the latest attached files as there was a slight modification on the logo Added Wednesday, March 1, 2017

minor update on the logo files in JPG and PSD has been updated kindly follow the new attachments. Added Thursday, March 2, 2017

Target Market(s)

modern minimalist clients

Industry/Entity Type

Design Agency

Requirements
Must have
• the logo
Nice to have
• i like the colors in the colored 3D logo attached
Should not have
• too many colors

```html
<!DOCTYPE html>
<html lang="en">
<head>
<meta charset="utf-8">
<title>Forma Atelier – Business Card</title>
<link rel="stylesheet" href="https://fonts.googleapis.com/css2?family=Open+Sans:wght@400;600;700&display=swap">
<style>
  :root {
    --backdrop: #e6e3df;
    --card: #f4f3f1;
    --card-edge: #d9d6d2;
    --ink: #2b2b2b;
    --ink-soft: #3d3d3d;
    --accent: #e2661c;
  }
  * { margin: 0; padding: 0; box-sizing: border-box; }
  html, body {
    width: 1200px; height: 969px; overflow: hidden;
    background: var(--backdrop);
    font-family: "Open Sans", Arial, sans-serif;
  }
  .card {
    position: absolute; left: 100px; top: 198px;
    width: 1000px; height: 572px;
    background: var(--card);
    border: 1px solid var(--card-edge);
    border-radius: 8px 8px 8px 8px;
    border-top-left-radius: 40px;
    color: var(--ink-soft);
  }
  .wordmark {
    position: absolute; left: 80px; top: 78px;
    font-size: 46px; font-weight: 700; letter-spacing: 2px;
    color: var(--ink); text-transform: uppercase; line-height: 1;
  }
  .byline {
    position: absolute; left: 82px; top: 136px;
    font-size: 24px; font-weight: 400; letter-spacing: 9px;
    color: var(--accent); text-transform: uppercase; line-height: 1;
  }
  .person { position: absolute; left: 80px; top: 180px; }
  .person__name {
    font-size: 34px; font-weight: 600; color: var(--accent); line-height: 1.2;
  }
  .person__role { font-size: 25px; color: var(--ink); line-height: 1.3; }
  .address {
    position: absolute; left: 80px; top: 282px;
    font-size: 25px; line-height: 1.45; font-style: normal; color: var(--ink-soft);
  }
  .contacts {
    position: absolute; left: 80px; top: 376px; list-style: none;
    font-size: 24px; line-height: 39px; color: var(--ink-soft);
  }
  .contacts li { display: flex; align-items: center; gap: 16px; }
  .contacts svg { width: 22px; height: 22px; fill: var(--accent); flex: none; }
  .brand-mark {
    position: absolute; right: 56px; top: 40px; bottom: 40px; width: 260px;
    display: flex; flex-direction: column; align-items: center; justify-content: center; gap: 28px;
  }
  .brand-mark__square { width: 150px; height: 150px; background: var(--accent); }
  .brand-mark__name {
    font-size: 30px; font-weight: 700; color: var(--ink);
    letter-spacing: 3px; text-transform: uppercase; text-align: center; line-height: 1.2;
  }
</style>
</head>
<body>
  <div class="card">
    <div class="wordmark">Forma Atelier</div>
    <div class="byline">By Lucien Marrow</div>

    <div class="person">
      <div class="person__name">ADAM REYES</div>
      <div class="person__role">CEO&amp;Founder</div>
    </div>

    <address class="address">2140 Cedar Hollow Road<br>Juneau, Alaska 99801</address>

    <ul class="contacts">
      <li>
        <svg viewBox="0 0 24 24" aria-hidden="true"><path d="M6.6 10.8a15.1 15.1 0 0 0 6.6 6.6l2.2-2.2c.3-.3.7-.4 1-.2 1.1.4 2.3.6 3.6.6.6 0 1 .4 1 1V20c0 .6-.4 1-1 1A17 17 0 0 1 3 4c0-.6.4-1 1-1h3.5c.6 0 1 .4 1 1 0 1.3.2 2.5.6 3.6.1.3 0 .7-.2 1z"/></svg>
        (555) 014 2738
      </li>
      <li>
        <svg viewBox="0 0 24 24" aria-hidden="true"><path d="M7 1h10a2 2 0 0 1 2 2v18a2 2 0 0 1-2 2H7a2 2 0 0 1-2-2V3a2 2 0 0 1 2-2zm0 3v14h10V4zm5 15.2a1.2 1.2 0 1 0 0 2.4 1.2 1.2 0 0 0 0-2.4z"/></svg>
        (555) 019 4406
      </li>
      <li>
        <svg viewBox="0 0 24 24" aria-hidden="true"><path d="M2 5h20v14H2zm2 2v.5l8 5 8-5V7zm0 2.8V17h16V9.8l-8 5z"/></svg>
        adam@formaatelier.com
      </li>
      <li>
        <svg viewBox="0 0 24 24" aria-hidden="true"><path d="M12 2a10 10 0 1 0 0 20 10 10 0 0 0 0-20zm6.9 6h-3a15 15 0 0 0-1.3-3.8A8 8 0 0 1 18.9 8zM12 4c.9 1.2 1.6 2.5 2 4h-4c.4-1.5 1.1-2.8 2-4zM4.3 14a8 8 0 0 1 0-4h3.4a16 16 0 0 0 0 4zm.8 2h3a15 15 0 0 0 1.3 3.8A8 8 0 0 1 5.1 16zm3-8h-3a8 8 0 0 1 4.3-3.8A15 15 0 0 0 8.1 8zM12 20c-.9-1.2-1.6-2.5-2-4h4c-.4 1.5-1.1 2.8-2 4zm2.3-6H9.7a14 14 0 0 1 0-4h4.6a14 14 0 0 1 0 4zm.3 5.8a15 15 0 0 0 1.3-3.8h3a8 8 0 0 1-4.3 3.8zm1.7-5.8a16 16 0 0 0 0-4h3.4a8 8 0 0 1 0 4z"/></svg>
        www.formaatelier.com
      </li>
    </ul>

    <div class="brand-mark">
      <div class="brand-mark__square"></div>
      <div class="brand-mark__name">Forma<br>Atelier</div>
    </div>
  </div>
</body>
</html>
```